Brookvane Consulting Business Card Design

Business Card Design for Brookvane Consulting. Brookvane Consulting is a boutique consultancy based in Atlanta, GA., that specializes in marketing strategy, organization planning, and leadership development. We provide solutions for small businesses and startups as well as Vantage 300 companies.

http://brookvaneconsulting.com/

Target Market(s)

We provide solutions for small businesses and startups as well as Vantage 300 companies.

Industry/Entity Type

Consulting

Contact Information for Business Card

Two sided business card with priority on contact information, logo, tag line (Motivation to Aim Higher, Act Bolder, Grow Further)

Colors

Designer to choose colors to be used in the design.

Requirements
Must have
• contact information, logo, tag line (Motivation to Aim Higher, Act Bolder, Grow Further)
• Simple no over communication.
Nice to have
• I would like to see different placements of logo and creative use of both sides of the card
Should not have
• Do not put too much information on the card.

```html
<!DOCTYPE html>
<html lang="en">
<head>
<meta charset="utf-8">
<title>Brookvane Consulting Business Card</title>
<link rel="stylesheet" href="https://fonts.googleapis.com/css2?family=Roboto+Condensed:wght@400;700&display=swap">
<style>
  :root {
    --canvas: #e6e4e0;
    --card-dark: #1c1c1d;
    --card-mid: #2f3031;
    --swoosh: #a9aaab;
    --swoosh-light: #d8d8d8;
    --swoosh-deep: #8e8f90;
    --text-white: #ffffff;
    --text-soft: #c9c9c9;
    --divider: #5a5b5c;
  }
  * { margin: 0; padding: 0; box-sizing: border-box; }
  html, body { width: 1200px; height: 911px; overflow: hidden; }
  body {
    background: var(--canvas);
    position: relative;
    font-family: "Roboto Condensed", Arial, sans-serif;
  }
  .card {
    position: absolute;
    width: 620px;
    height: 354px;
    border-radius: 6px;
    overflow: hidden;
    box-shadow: 0 12px 30px rgba(0,0,0,.25);
  }
  .card-front {
    left: 60px; top: 70px;
    background: linear-gradient(135deg, var(--card-mid) 0%, var(--card-dark) 70%);
  }
  .card-back {
    left: 520px; top: 487px;
    background: var(--card-dark);
  }
  .front-swoosh { position: absolute; inset: 0; }
  .brand {
    position: absolute;
    display: flex;
    align-items: center;
    gap: 10px;
    color: var(--text-white);
    font-weight: 400;
    letter-spacing: 0.04em;
    white-space: nowrap;
  }
  .brand-mark {
    width: 12px; height: 12px;
    background: var(--text-white);
  }
  .card-front .brand { left: 40px; bottom: 62px; font-size: 30px; }
  .front-divider {
    position: absolute;
    left: 310px; top: 40px;
    width: 1px; height: 150px;
    background: var(--divider);
  }
  .contact {
    position: absolute;
    left: 332px; top: 40px;
    color: var(--text-soft);
    font-size: 15px;
    line-height: 1.55;
  }
  .contact-name {
    color: var(--text-white);
    font-size: 20px;
    font-weight: 700;
    letter-spacing: 0.03em;
    text-transform: uppercase;
  }
  .contact-role { color: var(--text-white); font-size: 16px; margin-bottom: 14px; }
  .back-pattern {
    position: absolute; inset: 0;
    background: linear-gradient(160deg, #2a2a2b 0%, #1a1a1b 100%);
  }
  .card-back .brand {
    left: 50%; top: 130px;
    transform: translateX(-50%);
    font-size: 36px;
  }
  .tagline {
    position: absolute;
    left: 0; right: 0; top: 214px;
    text-align: center;
    color: var(--text-soft);
    font-size: 17px;
    letter-spacing: 0.02em;
  }
</style>
</head>
<body>
  <section class="card card-front" aria-label="Card front">
    <svg class="front-swoosh" viewBox="0 0 620 354" preserveAspectRatio="none" aria-hidden="true">
      <path d="M620 0 L620 354 L360 354 C470 320 560 220 620 0 Z" fill="var(--swoosh)"/>
      <path d="M620 0 C575 190 500 300 380 354 L420 354 C520 300 590 200 620 0 Z" fill="var(--swoosh-light)"/>
      <path d="M620 40 C585 210 520 310 440 354 L620 354 Z" fill="var(--swoosh-deep)"/>
    </svg>
    <div class="brand"><span class="brand-mark"></span>Brookvane Consulting</div>
    <div class="front-divider"></div>
    <div class="contact">
      <p class="contact-name">Darius Whitfield</p>
      <p class="contact-role">Founder/Managing Director</p>
      <p>P. 470-555-0147</p>
      <p>darius@brookvaneconsulting.com</p>
      <p>www.brookvaneconsulting.com</p>
    </div>
  </section>

  <section class="card card-back" aria-label="Card back">
    <div class="back-pattern" role="img" aria-label="Subtle dark grid pattern background"></div>
    <div class="brand"><span class="brand-mark"></span>Brookvane Consulting</div>
    <p class="tagline">Motivation to Aim Higher, Act Bolder, Grow Further</p>
  </section>
</body>
</html>
```